Electrician Letterhead Design MVR

We need some letterhead for our bills and other papers.
Customer address is on the right side (Swiss format)
A4 format

Design should also be applicable on Cards

Target Market(s)

Private Customers, Small Business

Industry/Entity Type

Electrician

Other font styles liked:
• incised 901

Colors
00AB8E
00BBA5
67D7C9
C6EFE9
E9F9F6

```html
<!DOCTYPE html>
<html lang="en">
<head>
<meta charset="utf-8">
<title>MVR Letterhead</title>
<link href="https://fonts.googleapis.com/css2?family=Open+Sans:wght@400;700&display=swap" rel="stylesheet">
<style>
  :root {
    --teal: #1a9e8c;
    --teal-band: #22a08f;
    --ink: #555555;
    --ink-dark: #4a4a4a;
    --paper: #f7f7f7;
    --backdrop: #dedede;
    --signature: #1b2a45;
  }
  * { box-sizing: border-box; margin: 0; padding: 0; }
  html, body {
    width: 1153px;
    height: 1200px;
    overflow: hidden;
    background: var(--backdrop);
    font-family: "Open Sans", Arial, sans-serif;
  }
  .letterhead {
    position: absolute;
    left: 161px;
    top: 22px;
    width: 830px;
    height: 1156px;
    background: var(--paper);
    box-shadow: 0 6px 24px rgba(0,0,0,0.12);
  }
  .brand {
    position: absolute;
    left: 82px;
    top: 70px;
    display: flex;
    align-items: center;
    gap: 12px;
  }
  .brand-mark {
    width: 18px;
    height: 18px;
    background: var(--teal);
  }
  .brand-name {
    font-size: 64px;
    font-weight: 700;
    line-height: 1;
    color: var(--teal);
    letter-spacing: 1px;
  }
  .contact {
    position: absolute;
    right: 83px;
    top: 64px;
    width: 200px;
    font-size: 14px;
    line-height: 17px;
    color: var(--ink-dark);
  }
  .contact-address { margin-bottom: 9px; }
  .contact-line {
    display: flex;
    align-items: center;
    gap: 7px;
  }
  .contact-line svg { width: 13px; height: 13px; flex: none; }
  .letter-body {
    position: absolute;
    left: 82px;
    top: 284px;
    width: 665px;
    font-size: 15.4px;
    line-height: 21.8px;
    color: var(--ink);
  }
  .letter-body p { margin-bottom: 21.8px; }
  .letter-body .paragraph { text-align: justify; }
  .signature {
    width: 100px;
    height: 90px;
    margin-top: 8px;
    background: linear-gradient(135deg, rgba(27,42,69,0.15), rgba(27,42,69,0.05));
    border-radius: 4px;
  }
  .footer-band {
    position: absolute;
    left: 0;
    right: 0;
    bottom: 0;
    height: 12px;
    background: var(--teal-band);
  }
</style>
</head>
<body>
  <main class="letterhead">
    <header>
      <div class="brand">
        <span class="brand-mark"></span>
        <span class="brand-name">MVR</span>
      </div>
      <address class="contact" style="font-style:normal">
        <div class="contact-address">Lindenweg 14 04109<br>City Rehfeld Germany</div>
        <div class="contact-line">
          <svg viewBox="0 0 16 16" aria-hidden="true"><path fill="var(--teal)" d="M2 6c0-2 2.5-3 6-3s6 1 6 3v1h-3V5.5H5V7H2zM4 8h8l1 6H3z"/><circle cx="8" cy="11" r="1.6" fill="#fff"/></svg>
          <span>555.010.4721</span>
        </div>
        <div class="contact-line">
          <svg viewBox="0 0 16 16" aria-hidden="true"><rect x="1" y="4" width="14" height="9" fill="var(--teal)"/><path d="M1 4l7 5 7-5" fill="none" stroke="#fff" stroke-width="1.3"/></svg>
          <span>info@mervalo-elektro.com</span>
        </div>
        <div class="contact-line">
          <svg viewBox="0 0 16 16" aria-hidden="true"><circle cx="8" cy="8" r="7" fill="var(--teal)"/><path d="M4 5c2 0 2 2 4 2s1 3-1 4M10 3c0 2 2 2 3 3" fill="none" stroke="#fff" stroke-width="1.2"/></svg>
          <span>www.mervalo-elektro.com</span>
        </div>
      </address>
    </header>

    <section class="letter-body">
      <p>Dear customer,</p>
      <p class="paragraph">Lorem ipsum dolor sit amet, consectetur adipisicing elit, sed do eiusmod tempor incididunt ut labore et dolore magna aliqua. Ut enim ad minim veniam, quis nostrud exercitation ullamco laboris nisi ut aliquip ex ea commodo consequat. Duis aute irure dolor in reprehenderit in voluptate velit esse cillum dolore eu fugiat nulla pariatur. Excepteur sint occaecat cupidatat non proident, sunt in culpa qui officia deserunt mollit anim id est laborum.</p>
      <p class="paragraph">Lorem ipsum dolor sit amet, consectetur adipisicing elit, sed do eiusmod tempor incididunt ut labore et dolore magna aliqua. Ut enim ad minim veniam, quis nostrud exercitation ullamco laboris nisi ut aliquip ex ea commodo consequat. Duis aute irure dolor in reprehenderit in voluptate velit esse cillum dolore eu fugiat nulla pariatur. Excepteur sint occaecat cupidatat non proident, sunt in culpa qui officia deserunt mollit anim id est laborum.</p>
      <p class="paragraph">Lorem ipsum dolor sit amet, consectetur adipisicing elit, sed do eiusmod tempor incididunt ut labore et dolore magna aliqua. Ut enim ad minim veniam, quis nostrud exercitation ullamco laboris nisi ut aliquip ex ea commodo consequat. Duis aute irure dolor in reprehenderit in voluptate velit esse cillum dolore eu fugiat nulla pariatur. Excepteur sint occaecat cupidatat non proident, sunt in culpa qui officia deserunt mollit anim id est laborum.</p>
      <p class="paragraph">Lorem ipsum dolor sit amet, consectetur adipisicing elit, sed do eiusmod tempor incididunt ut labore et dolore magna aliqua. Ut enim ad minim veniam, quis nostrud exercitation ullamco laboris nisi ut aliquip ex ea commodo consequat. Duis aute irure dolor in reprehenderit.</p>
      <p>Yours Sincerely,</p>
      <div class="signature" role="img" aria-label="Handwritten signature"></div>
    </section>

    <div class="footer-band"></div>
  </main>
</body>
</html>
```